Business Card For Halvenmoor Financial Consulting

Hi, I would like a business card designed. Bold, modern.
Please use the same design as the logo. I have also attached the website design to see the overall theme.
Wordmark Font
Color: Hex: #01AEF7

```html
<!DOCTYPE html>
<html lang="en">
<head>
<meta charset="utf-8">
<title>Halvenmoor Financial Consulting – Business Card</title>
<link rel="stylesheet" href="https://fonts.googleapis.com/css2?family=Montserrat:wght@400;500;700&display=swap">
<style>
  :root {
    --page-bg: #d9dcdf;
    --card-bg: #14202b;
    --accent: #01aef7;
    --text-light: #ffffff;
    --card-shadow: rgba(0, 0, 0, 0.28);
  }
  * { box-sizing: border-box; margin: 0; padding: 0; }
  html, body {
    width: 1200px;
    height: 900px;
    overflow: hidden;
    background: var(--page-bg);
    font-family: "Montserrat", Arial, sans-serif;
  }
  .canvas {
    position: relative;
    width: 1200px;
    height: 900px;
  }
  .card {
    position: absolute;
    left: 290px;
    width: 620px;
    height: 354px;
    background: var(--card-bg);
    box-shadow: 0 14px 30px var(--card-shadow);
    overflow: hidden;
  }
  .card--front { top: 70px; }
  .card--back { top: 476px; }

  /* Brand name block */
  .brand {
    display: flex;
    align-items: center;
    gap: 16px;
    color: var(--text-light);
  }
  .brand__square {
    width: 44px;
    height: 44px;
    background: var(--accent);
    flex: none;
  }
  .brand__name {
    font-weight: 700;
    text-transform: uppercase;
    letter-spacing: 0.04em;
    line-height: 1.1;
    white-space: nowrap;
  }
  .card--front .brand {
    position: absolute;
    left: 50%;
    top: 50%;
    transform: translate(-50%, -50%);
  }
  .card--front .brand__name { font-size: 30px; }
  .card--back .brand {
    position: absolute;
    left: 28px;
    top: 228px;
    gap: 10px;
  }
  .card--back .brand__square { width: 28px; height: 28px; }
  .card--back .brand__name { font-size: 13px; }

  /* Divider strokes */
  .divider {
    position: absolute;
    left: 262px;
    top: 90px;
    width: 120px;
    height: 200px;
  }
  .divider line { stroke: var(--accent); stroke-width: 1.4; }

  /* Contact details */
  .details {
    position: absolute;
    left: 392px;
    top: 70px;
    color: var(--text-light);
    white-space: nowrap;
  }
  .details__name {
    color: var(--accent);
    font-weight: 700;
    font-size: 21px;
    text-transform: uppercase;
    letter-spacing: 0.01em;
  }
  .details__title {
    font-size: 14px;
    font-weight: 500;
    margin-top: 2px;
  }
  .details__address {
    font-size: 13px;
    line-height: 1.35;
    margin-top: 16px;
  }
  .contact-list {
    list-style: none;
    margin-top: 18px;
  }
  .contact-list__item {
    display: flex;
    align-items: center;
    gap: 9px;
    font-size: 13px;
    margin-bottom: 9px;
  }
  .contact-list__icon { width: 20px; height: 20px; flex: none; }
</style>
</head>
<body>
<main class="canvas">

  <section class="card card--front" aria-label="Card front">
    <div class="brand">
      <span class="brand__square"></span>
      <span class="brand__name">Halvenmoor<br>Financial Consulting</span>
    </div>
  </section>

  <section class="card card--back" aria-label="Card back">
    <div class="brand">
      <span class="brand__square"></span>
      <span class="brand__name">Halvenmoor<br>Financial Consulting</span>
    </div>

    <svg class="divider" viewBox="0 0 120 200" aria-hidden="true">
      <line x1="58" y1="4" x2="10" y2="196"/>
      <line x1="92" y1="30" x2="52" y2="180"/>
      <line x1="112" y1="14" x2="62" y2="198"/>
    </svg>

    <div class="details">
      <h1 class="details__name">Elena Rowcliffe</h1>
      <p class="details__title">Senior Consultant</p>
      <p class="details__address">45-12 Linden Ave 8<br>Ridgefield, NY 11402</p>
      <ul class="contact-list">
        <li class="contact-list__item">
          <svg class="contact-list__icon" viewBox="0 0 20 20" aria-hidden="true">
            <circle cx="10" cy="10" r="10" fill="var(--accent)"/>
            <path d="M6.5 5.5l2 0 1 2.5-1.3 1a6 6 0 0 0 2.8 2.8l1-1.3 2.5 1v2a1 1 0 0 1-1 1A8.5 8.5 0 0 1 5.5 6.5a1 1 0 0 1 1-1z" fill="#fff"/>
          </svg>
          +1 555 014 2290
        </li>
        <li class="contact-list__item">
          <svg class="contact-list__icon" viewBox="0 0 20 20" aria-hidden="true">
            <circle cx="10" cy="10" r="10" fill="var(--accent)"/>
            <rect x="5" y="6.5" width="10" height="7" fill="#fff"/>
            <path d="M5 6.5l5 4 5-4" fill="none" stroke="var(--accent)" stroke-width="1"/>
          </svg>
          info@halvenmoor.com
        </li>
        <li class="contact-list__item">
          <svg class="contact-list__icon" viewBox="0 0 20 20" aria-hidden="true">
            <circle cx="10" cy="10" r="10" fill="var(--accent)"/>
            <circle cx="10" cy="10" r="5" fill="none" stroke="#fff" stroke-width="1.2"/>
            <ellipse cx="10" cy="10" rx="2.2" ry="5" fill="none" stroke="#fff" stroke-width="1"/>
            <line x1="5" y1="10" x2="15" y2="10" stroke="#fff" stroke-width="1"/>
          </svg>
          www.halvenmoor.com
        </li>
      </ul>
    </div>
  </section>

</main>
</body>
</html>
```